Modern claims management company

We need a new company presentation brochure, composed of about 20 pages in A4 format.
Cover, page 1 who we are, page 2 company profile, page 3 territorial operation, page from 4 to 10 services offered and description of services (The title of the page are: Perizie e Liquidazione danni, riparazioni e sostituzioni, teleclaimer, accertamento danni da fenomeno elettrico, TPA, Auditing, drone pilot, Valutazione rischi), from 11 to 17 specializations (Sinistri gravi, R.C., Tecnologici, Energie rinnovabili, strutture, ambiente) page 18 e 19 integrated services (perdite occulte, ricerca guasti, indagini termografiche, crisis management), page 20 clients ( list companies and logos) page 21 contact.
The company is made up of various companies, which belong to the principal, each of which deals with specific activities.
To date we already have various logos of the main company (Varesco and Tundi) as well as the logos of the other companies. I load them on the portal.
Found then the graphic solution that we like we will have to proceed to make a presentation in similar powerpoint and the website.

Target Market(s)

Insurance Company, Insurance Broker

Font styles to use
Other font styles liked:
• ARIAL

Colors
333333
5c5c5c
959595
0392cd

Requirements
Must have
• It must be clear, professional and modern.
Nice to have
• I indicate some competitor sites, so that you can better understand what we are doing. www.brantows.com, www.pemberwellhastons.com, www.ortevisandri.com, www.gruppotavesi.com, www.varduzzo.eu.

```html
<!DOCTYPE html>
<html lang="en">
<head>
<meta charset="utf-8">
<title>Varesco and Tundi — Our services spread</title>
<link href="https://fonts.googleapis.com/css2?family=Ubuntu:ital,wght@0,400;0,700;1,400&display=swap" rel="stylesheet">
<style>
  :root {
    --backdrop: #2e2e30;
    --paper: #f1f2f6;
    --paper-shade: #e2e5ec;
    --brand-blue: #3a5f94;
    --brand-blue-dark: #2f5288;
    --accent-sky: #4fa6e0;
    --panel-grey: #5c5c5c;
    --text-dark: #333333;
    --text-mid: #5c5c5c;
    --text-light: #e4e4e4;
    --white: #ffffff;
  }
  * { margin: 0; padding: 0; box-sizing: border-box; }
  html, body {
    width: 1200px; height: 789px; overflow: hidden;
    background: var(--backdrop);
    font-family: "Ubuntu", Arial, sans-serif;
  }
  .spread {
    position: absolute; left: 60px; top: 12px;
    width: 1080px; height: 764px;
    display: flex;
  }
  .page {
    position: relative; width: 540px; height: 764px;
    overflow: hidden;
  }
  .page--left { background: linear-gradient(90deg, var(--paper) 70%, var(--paper-shade)); }
  .page--right { background: linear-gradient(90deg, var(--paper-shade), var(--paper) 30%); }
  .page-shapes { position: absolute; inset: 0; }

  .section-title {
    font-weight: 700; font-size: 21px; color: var(--brand-blue);
    letter-spacing: -0.2px;
  }
  .body-copy { font-size: 9.5px; line-height: 1.45; color: var(--text-dark); }
  .body-copy p + p { margin-top: 9px; }

  .intro { position: absolute; left: 42px; top: 42px; width: 400px; }
  .intro .body-copy { margin-top: 10px; }

  .photo {
    position: absolute; left: 38px; top: 300px; width: 450px; height: 222px;
    background: linear-gradient(100deg, #23262e 0%, #3a3e48 35%, #8d949c 55%, #d5dadf 80%, #eef1f3 100%);
  }
  .photo-rule {
    position: absolute; left: 38px; top: 522px; width: 450px; height: 6px;
    background: var(--brand-blue);
  }
  .caption { position: absolute; left: 42px; top: 548px; width: 380px; }

  .feature-panel {
    position: absolute; left: 58px; top: 112px; width: 410px; height: 412px;
    background: var(--panel-grey); padding: 26px 28px;
  }
  .feature-panel .section-title { color: var(--white); font-size: 19px; }
  .feature-panel .body-copy { color: var(--text-light); margin-top: 10px; }
  .pull-quote {
    position: relative; margin: 24px 8px 0 30px;
    font-style: italic; font-size: 13px; line-height: 1.5; color: var(--white);
  }
  .pull-quote .mark {
    position: absolute; font-family: Georgia, serif; font-style: normal;
    font-size: 46px; line-height: 1; color: var(--white);
  }
  .pull-quote .mark--open { left: -32px; top: -6px; }
  .pull-quote .mark--close { right: 0; bottom: -44px; }

  .info-band {
    position: absolute; left: 0; top: 572px; width: 472px; height: 104px;
    background: var(--brand-blue); padding: 14px 26px 0 70px;
  }
  .info-band .body-copy { color: var(--text-light); }
</style>
</head>
<body>
<main class="spread">
  <section class="page page--left">
    <svg class="page-shapes" width="540" height="764" viewBox="0 0 540 764" aria-hidden="true">
      <path d="M395 0 Q470 25 540 125 L540 0 Z" fill="var(--brand-blue)"/>
      <path d="M455 540 L540 540 L540 640 L470 640 Z" fill="var(--brand-blue-dark)"/>
    </svg>
    <div class="intro">
      <h1 class="section-title">Our services</h1>
      <div class="body-copy">
        <p>Lorem ipsum dolor sit amet, consectetuer adipiscing elit, sed diam nonummy nibh euismod tincidunt ut laoreet dolore magna aliquam erat volutpat. Ut wisi enim ad minim veniam, quis nostrud exerci tation ullamcorper suscipit lobortis nisl ut aliquip ex ea commodo consequat.</p>
        <p>Duis autem vel eum iriure dolor in hendrerit in vulputate velit esse molestie consequat, vel illum dolore eu feugiat nulla facilisis at vero eros et accumsan et iusto odio dignissim qui blandit praesent luptatum zzril delenit augue duis dolore te feugait nulla facilisi.</p>
        <p>Lorem ipsum dolor sit amet, cons ectetuer adipiscing elit, sed diam nonummy nibh euismod tincidunt ut laoreet dolore magna aliquam erat volutpat. Ut wisi enim ad minim veniam, quis nostrud exerci tation ullamcorper suscipit lobortis nisl ut aliquip ex ea commodo consequat.</p>
      </div>
    </div>
    <div class="photo" role="img" aria-label="Photo of three business people in suits looking ahead in front of a modern office building"></div>
    <div class="photo-rule"></div>
    <div class="caption body-copy">
      <p>Lorem ipsum dolor sit amet, consectetuer adipiscing elit, sed diam nonummy nibh euismod tincidunt ut laoreet dolore magna aliquam erat volutpat. Ut wisi enim ad minim veniam.</p>
    </div>
  </section>

  <section class="page page--right">
    <svg class="page-shapes" width="540" height="764" viewBox="0 0 540 764" aria-hidden="true">
      <path d="M0 30 Q10 0 60 0 L540 0 L540 470 L490 470 L490 96 L0 96 Z" fill="var(--brand-blue)"/>
      <path d="M0 100 L46 100 L40 110 L0 110 Z" fill="var(--accent-sky)"/>
      <path d="M476 476 L540 476 L540 486 L470 486 Z" fill="var(--accent-sky)"/>
      <path d="M0 572 L60 572 L60 676 L0 690 Z" fill="var(--brand-blue-dark)"/>
    </svg>
    <div class="feature-panel">
      <h2 class="section-title">Our services</h2>
      <div class="body-copy">
        <p>Lorem ipsum dolor sit amet, consectetuer adipiscing elit, sed diam nonummy nibh euismod tincidunt ut laoreet dolore magna aliquam erat volutpat. Ut wisi enim ad minim veniam, quis nostrud exerci tation ullamcorper suscipit lobortis nisl ut aliquip.</p>
        <p>Duis autem vel eum iriure dolor in hendrerit in vulputate velit esse molestie consequat, vel illum dolore eu feugiat nulla facilisis at vero eros et accumsan et iusto odio dignissim qui blandit praesent luptatum zzril delenit augue duis dolore te feugait nulla facilisi.</p>
        <p>Lorem ipsum dolor sit amet, cons ectetuer adipiscing elit, sed diam nonummy nibh euismod tincidunt ut laoreet dolore magna aliquam erat volutpat. Ut wisi enim ad minim veniam, quis nostrud exerci tation.</p>
      </div>
      <blockquote class="pull-quote">
        <span class="mark mark--open">&ldquo;</span>
        Lorem ipsum dolor sit amet, consectetuer adipiscing elit, sed diam nonummy nibh euismod tincidunt ut laoreet dolore magna
        <span class="mark mark--close">&rdquo;</span>
      </blockquote>
    </div>
    <div class="info-band body-copy">
      <p>Lorem ipsum dolor sit amet, consectetuer adipiscing elit, sed diam nonummy nibh euismod tincidunt ut laoreet dolore magna aliquam erat volutpat. Ut wisi enim ad minim veniam, quis nostrud exerci tation ullamcorper suscipit lobortis nisl ut aliquip ex ea commodo consequat. Ut wisi enim ad minim veniam, quis nostrud exerci tation.</p>
    </div>
  </section>
</main>
</body>
</html>
```